Project Lists Banner for HVAC ecommerce store

We want a banner that showcases our project list feature that will allow customers to create list of products that they can select and quickly order. this will be a middle of page banner. It will replace this banner - https://www.lumapixvault.com/image/84730295
Font: Noto Sans
Size: 938x300 px
Color Options: #0059E, #00BBE3, #C6C8C7
Text:
Create lists of frequently purchased SKU's for fast ordering.
- Warehouse Inventory
- Complete Systems
- Large Projects
- And More...
"Sign In" is the call to action button. make button with non rounded (square) boarders.
We don't want a computer screen in banner nor a person. You can look at our competitors below for ideas.
Our staging server is belfarq7.com for reference
Our competitors:
https://www.brantlowholdings.com/
https://www.folvexa.com/
https://www.zelbrk.com/
https://www.vostrel.com/index.html
HVAC, B2B
HVAC

```html
<!DOCTYPE html>
<html lang="en">
<head>
<meta charset="utf-8">
<title>Project Lists Banner</title>
<link href="https://fonts.googleapis.com/css2?family=Noto+Sans:wght@400;600;700;800&display=swap" rel="stylesheet">
<style>
:root{
  --page-bg:#e4e5e7;
  --navy:#083a76;
  --blue-mid:#0a57a8;
  --blue-bright:#0077c8;
  --cyan:#00b5e2;
  --cta:#1db3e4;
  --cta-text:#0d2340;
  --white:#ffffff;
  --icon:#2aa6e0;
  --ui-border:#d7d9dc;
  --ui-text:#333a44;
  --ui-muted:#7b828c;
  --ui-header:#0b4a98;
  --ui-orange:#f07a1c;
  --ui-green:#4a9a4a;
  --ui-btn-dark:#4a4f57;
  --ui-btn-soft:#8fb1d8;
  --ui-icon:#555555;
}
*{box-sizing:border-box;margin:0;padding:0}
html,body{width:1200px;height:636px;overflow:hidden}
body{background:var(--page-bg);font-family:"Noto Sans",sans-serif;position:relative}
.banner{position:absolute;left:89px;top:149px;width:1024px;height:328px;overflow:hidden;
  background:var(--navy);box-shadow:0 10px 14px rgba(0,0,0,.28)}
.banner-shapes{position:absolute;inset:0}
.headline{position:absolute;left:34px;top:26px;color:var(--white);font-weight:700;font-size:29px;line-height:36px;letter-spacing:.1px}
.features{position:absolute;left:35px;top:142px;list-style:none;color:var(--white);font-size:22px;line-height:31px}
.features li{display:flex;align-items:center;gap:19px}
.features svg{width:17px;height:17px;flex:none}
.cta{position:absolute;left:34px;top:256px;width:204px;height:39px;background:var(--cta);color:var(--cta-text);
  font-weight:600;font-size:22px;display:flex;align-items:center;justify-content:center;letter-spacing:.3px;text-decoration:none}

.app{position:absolute;left:480px;top:37px;width:511px;height:254px;background:var(--white);color:var(--ui-text);font-size:5px;overflow:hidden}
.app-sidebar{position:absolute;left:0;top:0;width:101px;height:254px;border-right:1px solid var(--ui-border)}
.sidebar-title{font-size:6.5px;font-weight:600;padding:11px 9px 7px;border-bottom:1px solid var(--ui-border)}
.sidebar-menu{list-style:none;padding:4px 9px;line-height:8.6px;font-size:4.3px;color:var(--ui-muted)}
.sidebar-menu .active{color:var(--ui-header);text-decoration:underline}
.import-box{position:absolute;left:5px;top:145px;width:91px;height:93px;border:1px solid var(--ui-border);padding:5px}
.import-title{font-size:5px;font-weight:600;display:flex;align-items:center;gap:3px}
.import-title .dot{width:7px;height:7px;border-radius:50%;background:var(--ui-green);display:inline-block}
.dropzone{margin-top:6px;border:1px dashed #b8bcc2;height:54px;text-align:center;font-size:3.8px;line-height:5px;padding:4px 3px;color:var(--ui-muted)}
.btn-choose{display:block;margin:3px auto;width:52px;height:9px;background:var(--ui-header);color:var(--white);font-size:4px;line-height:9px}
.link{color:var(--ui-header);text-decoration:underline}
.btn-tutorial{display:block;margin:5px auto 0;width:52px;height:10px;background:var(--ui-orange);color:var(--white);font-size:4px;line-height:10px;text-align:center}

.app-main{position:absolute;left:106px;top:0;width:402px;height:254px}
.main-title{position:absolute;left:0;top:7px;font-size:9px;font-weight:600}
.print{position:absolute;right:0;top:10px;font-size:4.5px;color:var(--ui-header)}
.project-bar{position:absolute;left:0;top:36px;width:402px;height:11px;background:var(--ui-header);color:var(--white);font-size:5.5px;font-weight:700;padding:0 5px;line-height:11px}
.project-bar span{float:right;font-size:4px;font-weight:600}
.field{position:absolute;height:15px;border:1px solid var(--ui-border);font-size:4.5px;padding:0 6px;line-height:13px;border-radius:2px}
.rule{position:absolute;left:5px;width:392px;height:1px;background:var(--ui-border)}
.btn{position:absolute;height:14px;color:var(--white);font-size:4.6px;font-weight:600;text-align:center;line-height:14px;border-radius:1px}
.table{position:absolute;left:0;top:155px;width:402px}
.table-head{height:12px;border-bottom:1px solid var(--ui-border);display:flex;align-items:center;font-size:4.5px;font-weight:600;position:relative}
.row{height:21px;border-bottom:1px solid var(--ui-border);display:flex;align-items:center;position:relative}
.check{width:6px;height:6px;border:1px solid #8a9098;margin-left:6px;flex:none}
.brand{margin-left:8px;width:16px;font-size:3.6px;font-weight:700;color:var(--ui-header);flex:none}
.product{margin-left:3px;font-size:4.3px;line-height:5.6px;width:210px}
.product b{font-weight:700;display:block}
.qty{position:absolute;left:256px;display:flex;gap:2px;align-items:center}
.qty i{width:13px;height:13px;background:var(--ui-btn-dark);color:var(--white);font-style:normal;font-size:6px;text-align:center;line-height:13px}
.qty span{width:14px;height:13px;border:1px solid var(--ui-border);text-align:center;line-height:11px;font-size:4.5px}
.sell{position:absolute;left:314px;font-size:4.3px}
.mine{position:absolute;left:353px;font-size:4.3px;display:flex;gap:3px;align-items:center}
.mine span{width:24px;height:13px;border:1px solid var(--ui-border);line-height:11px;padding-left:2px}
.trash{position:absolute;left:388px;width:5px;height:6px;background:var(--ui-icon);border-radius:0 0 1px 1px}
</style>
</head>
<body>
<section class="banner" aria-label="Project Lists promotion">
  <svg class="banner-shapes" viewBox="0 0 1024 328" width="1024" height="328" aria-hidden="true">
    <polygon points="560,0 1024,0 1024,328 285,328" fill="var(--blue-mid)"/>
    <polygon points="680,0 1024,0 1024,150 470,328 290,328" fill="var(--cyan)"/>
    <polygon points="1024,150 1024,328 470,328" fill="var(--blue-bright)"/>
  </svg>

  <h1 class="headline">Create Project Lists of<br>frequency purchased SKU's<br>for fast ordering.</h1>

  <ul class="features">
    <li><svg viewBox="0 0 20 20" aria-hidden="true"><g stroke="var(--icon)" stroke-width="2" stroke-linecap="round"><line x1="10" y1="1" x2="10" y2="19"/><line x1="2.2" y1="5.5" x2="17.8" y2="14.5"/><line x1="2.2" y1="14.5" x2="17.8" y2="5.5"/></g></svg>Warehouse Inventory</li>
    <li><svg viewBox="0 0 20 20" aria-hidden="true"><g stroke="var(--icon)" stroke-width="2" stroke-linecap="round"><line x1="10" y1="1" x2="10" y2="19"/><line x1="2.2" y1="5.5" x2="17.8" y2="14.5"/><line x1="2.2" y1="14.5" x2="17.8" y2="5.5"/></g></svg>Complete Systems</li>
    <li><svg viewBox="0 0 20 20" aria-hidden="true"><g stroke="var(--icon)" stroke-width="2" stroke-linecap="round"><line x1="10" y1="1" x2="10" y2="19"/><line x1="2.2" y1="5.5" x2="17.8" y2="14.5"/><line x1="2.2" y1="14.5" x2="17.8" y2="5.5"/></g></svg>Large Projects And More...</li>
  </ul>

  <a class="cta" href="#">SIGN IN</a>

  <div class="app" aria-label="Project lists account page">
    <aside class="app-sidebar">
      <div class="sidebar-title">My Account</div>
      <ul class="sidebar-menu">
        <li>DASHBOARD</li><li>PROFILE</li><li>ADDRESS BOOK</li><li>MANAGE USERS</li><li>INVOICE HISTORY</li>
        <li>ORDER HISTORY</li><li>STATEMENTS</li><li>MY QUOTES</li><li>FAVORITES</li><li class="active">PROJECT LISTS</li>
      </ul>
      <div class="import-box">
        <div class="import-title"><span class="dot"></span>Import Project Lists</div>
        <div class="dropzone">Drag and drop a .CSV file here, or select file from your computer.
          <span class="btn-choose">Choose File</span>
          <span class="link">Download Sample CSV</span>
        </div>
        <span class="btn-tutorial">Tutorial</span>
      </div>
    </aside>

    <div class="app-main">
      <div class="main-title">Project Lists</div>
      <div class="print">Print Projects</div>
      <div class="project-bar">Project:<span>Add New Project</span></div>
      <div class="field" style="left:5px;top:53px;width:196px">Main</div>
      <div class="rule" style="top:78px"></div>
      <div class="field" style="left:5px;top:88px;width:196px">Main</div>
      <div class="field" style="left:206px;top:88px;width:190px;height:20px"></div>
      <div class="rule" style="top:114px"></div>
      <div class="field" style="left:0;top:124px;width:134px">Enter Product Name or SKU to Add</div>
      <div class="btn" style="left:137px;top:124px;width:42px;background:var(--ui-btn-soft)">Add to List</div>
      <div class="field" style="left:310px;top:124px;width:52px">Select Action</div>
      <div class="btn" style="left:366px;top:124px;width:36px;background:var(--ui-header)">Apply</div>

      <div class="table">
        <div class="table-head"><div class="check"></div><span style="margin-left:9px">Product/SKU</span><span style="position:absolute;left:274px">Qty</span><span style="position:absolute;left:314px">Sell Price</span><span style="position:absolute;left:353px">My Price</span></div>
        <div class="row"><div class="check"></div><span class="brand">ARVEN</span><div class="product"><b>Hail Guard 6.5/12.5 Sentinel</b>AHG6571</div><div class="qty"><i>−</i><span>1</span><i>+</i></div><span class="sell">$413.00</span><div class="mine">$<span>413.00</span></div><i class="trash"></i></div>
        <div class="row"><div class="check"></div><span class="brand">ARVEN</span><div class="product"><b>Screwdriver, Combo, 6-In-1</b>SDR-5-61</div><div class="qty"><i>−</i><span>5</span><i>+</i></div><span class="sell">$9.00</span><div class="mine">$<span>9.00</span></div><i class="trash"></i></div>
        <div class="row"><div class="check"></div><span class="brand">ARVEN</span><div class="product"><b>Panel Seamer, Kestrow</b>PNL-SEAM-01</div><div class="qty"><i>−</i><span>10</span><i>+</i></div><span class="sell">$50.00</span><div class="mine">$<span>50.00</span></div><i class="trash"></i></div>
        <div class="row"><div class="check"></div><span class="brand">ARVEN</span><div class="product"><b>Condenser Mounting Brackets, 1/8" Steel, SMLB Per Pair</b>CMB-ACB-42</div><div class="qty"><i>−</i><span>5</span><i>+</i></div><span class="sell">$31.00</span><div class="mine">$<span>31.00</span></div><i class="trash"></i></div>
      </div>
    </div>
  </div>
</section>
</body>
</html>
```